Website redesign for KestrelFinanceMan/TKFinanceMan

Job Title: Talented Web Designer for SEO-Friendly Website Creation & HostFalcon cPanel Integration
 
Inspiration: dunewheelracingexample.com
Pages:

About
Get a Quote
FAQ
Boat Loans
RV Loans
Testimonials
News/Blog
Affiliate Program
Contact

Job Description:
 
We are seeking a skilled and creative freelance web designer to build a stunning, SEO-optimized website for our business. The ideal candidate will have a strong design portfolio, technical expertise in creating search engine-friendly websites, and experience implementing websites into HostFalcon cPanel.
 
Project Overview:
 
Objective: Create a modern, motorsports themed visually appealing website that is optimized for SEO.

Platform: The site will be hosted on HostFalcon, so familiarity with their cPanel for setup and integration is essential.

Deliverables:
         •A fully functional website (desktop and mobile) with user-friendly navigation and a responsive design.
         •SEO best practices implemented throughout, including proper meta tags, optimized images, fast loading speeds, and mobile compatibility.
         •Seamless integration into HostFalcon cPanel for hosting.
         •Guidance or documentation on maintaining the site post-launch.
 
Key Skills Required:
 
         •Proficiency in web design (HTML, CSS, JavaScript, or relevant platforms like WordPress).
         •Knowledge of SEO principles and tools for website optimization.
         •Experience with HostFalcon cPanel, including file management and DNS settings.
         •Strong communication skills to understand our vision and provide progress updates.
 
What We’re Looking For:
 
         •A designer who can transform our ideas into a sleek and functional website.
         •Someone proactive in suggesting creative design elements and SEO improvements.
         •A reliable professional who can meet deadlines and deliver a polished product.
 
Please provide:
 
         1.A brief introduction and why you’re a good fit for this project.
         2.Examples of previous web design projects, especially those with SEO implementation.
         3.Your estimated timeline and cost for this project.
 
We are excited to work with a talented designer who can bring our vision to life. If you are passionate about web design and SEO, we’d love to hear from you!

Target Market(s)

Boat and RV buyers looking for a loan

Coding

Coded - Design and coding required

Number of Pages Required

5+ page

Colors
F0912C
F2A743
F7CA91
FBE8D2
FDF5EE

Requirements
Must have
• motorsports type design
Nice to have
• fcontact forms easy to use layout on brand and color scheme of kestrelfinanceman and tkfinanceman.example

```html
<!DOCTYPE html>
<html lang="en">
<head>
<meta charset="utf-8">
<title>TKFinanceMan — RV Loans Made Easy</title>
<link href="https://fonts.googleapis.com/css2?family=Orbitron:wght@700;800&family=Roboto:wght@400;500;700;900&display=swap" rel="stylesheet">
<style>
:root{
  --orange:#F0912C;
  --orange-deep:#EE6A1F;
  --amber:#F2A743;
  --sand:#F7CA91;
  --cream:#FBE8D2;
  --paper:#FDF5EE;
  --blue:#1E88E5;
  --blue-dark:#1565C0;
  --charcoal:#3F4145;
  --card:#4A4C50;
  --ink:#222;
  --night:#161718;
  --white:#fff;
}
*{box-sizing:border-box;margin:0;padding:0}
html,body{width:1200px;height:4352px;overflow:hidden}
body{position:relative;background:var(--white);font-family:'Roboto',Arial,sans-serif;color:var(--ink)}
.abs{position:absolute}
.display{font-family:'Orbitron','Roboto',sans-serif}

/* header */
.brand{left:24px;top:12px;font:900 24px/34px 'Roboto',sans-serif;color:var(--orange);white-space:nowrap}
.main-nav{left:150px;top:58px;height:40px;width:915px;background:#2f3033;display:flex;align-items:center;padding-left:6px}
.main-nav a{color:var(--white);font-size:15px;text-decoration:none;padding:0 15px;line-height:40px;white-space:nowrap}
.main-nav a.active{background:var(--blue)}
.call{left:780px;top:10px;display:flex;align-items:center;gap:8px;color:var(--white)}
.call small{display:block;font-size:11px;color:var(--orange);font-weight:700}
.call b{font-size:20px}
.btn{display:inline-block;border-radius:24px;font-weight:700;color:var(--white);text-align:center;text-decoration:none}
.btn-blue{background:var(--blue)}
.btn-orange{background:var(--orange-deep)}
.quote-btn{left:975px;top:14px;width:140px;height:36px;line-height:36px;font-size:14px}

/* hero */
.hero-photo{left:0;top:0;width:1200px;height:690px;background:linear-gradient(180deg,#3a3d42 0%,#5c7da3 15%,#8fa9c4 40%,#6f7378 70%,#4d5156 100%)}
.hero-curve{left:0;top:520px}
.hero-title{left:40px;top:280px;font:900 52px/60px 'Roboto',sans-serif;color:var(--white)}
.hero-sub{left:40px;top:350px;width:300px;font-size:15px;line-height:20px;color:var(--white)}
.hero-apply{left:40px;top:420px;width:150px;height:34px;line-height:34px;font-size:13px}
.hero-arrow{top:330px;color:var(--white);font-size:24px}

/* calculator */
.calc-field{top:752px;width:320px;height:46px;border:2px solid #cfd3d8;border-radius:24px;background:var(--white);font-size:16px;color:#444;padding:0 22px;display:flex;align-items:center;justify-content:space-between}
.calc-btn{left:495px;top:828px;width:210px;height:42px;line-height:42px;font-size:15px}
.coach-art{left:10px;top:830px;width:240px;height:140px;border-radius:16px;background:linear-gradient(135deg,#e9ebee,#9ea4ab)}

/* section heads */
.section-title{width:1200px;left:0;text-align:center;font:900 40px/48px 'Roboto',sans-serif;color:var(--orange-deep)}

/* rv cards */
.rv-card{width:320px;height:384px;border-radius:14px;background:var(--card);overflow:hidden;color:var(--white)}
.rv-card.featured{background:var(--blue);box-shadow:0 0 0 4px #cfe5fb}
.rv-card .thumb{height:186px;margin:10px;border-radius:10px}
.rv-card h3{font-size:22px;font-weight:700;margin:8px 18px 8px}
.rv-card p{font-size:13px;line-height:18px;margin:0 18px;color:#e6e6e6}
.rv-card .btn{position:absolute;left:18px;bottom:22px;width:120px;height:32px;line-height:32px;font-size:12px}

/* about */
.about-band{left:0;top:2020px}
.about-photo{left:130px;top:2170px;width:440px;height:440px;border-radius:50%;border:8px solid var(--white);background:linear-gradient(160deg,#b7c9d8 0%,#7c8f68 55%,#4b5a3a 100%)}
.about-copy{left:620px;top:2160px;width:470px;color:var(--white)}
.about-copy h2{font-size:44px;letter-spacing:2px}
.about-copy h4{font-size:22px;font-weight:500;margin:12px 0 14px}
.about-copy li{list-style:none;font-size:16px;line-height:26px;display:flex;align-items:center;gap:8px}
.tick{width:16px;height:16px;border-radius:3px;background:var(--white);display:inline-flex;align-items:center;justify-content:center}
.about-copy p{font-size:16px;line-height:22px;margin-top:4px}
.about-copy .btn{margin-top:16px;width:130px;height:36px;line-height:36px;font-size:13px}
.van-art{left:860px;top:2650px;width:300px;height:150px;border-radius:20px;background:linear-gradient(135deg,#f4f4f4,#b9bdc2)}

/* more than boats */
.flag-wash{left:0;top:3040px;width:600px;height:430px;background:linear-gradient(90deg,rgba(200,60,60,.10),rgba(30,80,170,.06),rgba(255,255,255,0))}
.lede{left:0;top:3058px;width:1200px;text-align:center;font-size:15px;color:#555}
.service{top:3110px;width:260px;text-align:center}
.service .disc{width:150px;height:150px;margin:0 auto;border-radius:50%;background:var(--blue);border:6px solid #cfe5fb;display:flex;align-items:center;justify-content:center}
.service span{display:block;margin-top:22px;font-size:20px;color:#222}
.contact-btn{left:530px;top:3360px;width:140px;height:40px;line-height:36px;border:2px solid var(--orange);color:var(--orange-deep);background:var(--white);font-size:14px}

/* testimonials */
.reviews{left:100px;top:3480px;width:1000px;height:460px;border-radius:28px;background:linear-gradient(180deg,#2196f3,#1565c0);color:var(--white);text-align:center}
.reviews h2{margin-top:50px;font-size:38px;letter-spacing:1px}
.avatar{width:90px;height:90px;border-radius:50%;background:#cfd8e3;margin:26px auto 10px;border:3px solid var(--white)}
.reviews h5{font-size:16px;font-weight:700}
.stars{color:var(--amber);font-size:20px;letter-spacing:3px}
.reviews p{width:860px;margin:8px auto 0;font-size:15px;line-height:22px}
.rev-arrow{top:180px;width:30px;height:30px;border-radius:50%;background:rgba(255,255,255,.2);line-height:30px;font-size:16px}

/* partners */
.partner{top:3992px;width:150px;height:80px;border-radius:6px;background:#f2f3f5}
.partner.active{border:3px solid #283b8a;background:var(--white)}
.partner i{position:absolute;left:25px;top:30px;width:100px;height:20px;border-radius:10px;background:#8a8d92}
.partner-arrow{top:4017px;width:30px;height:30px;border-radius:50%;background:#333;color:#fff;text-align:center;line-height:30px;font-size:14px}

/* footer */
.site-footer{left:0;top:4100px;width:1200px;height:220px;background:var(--night);color:#ddd}
.rv-art{left:950px;top:3960px;width:230px;height:134px;border-radius:16px;background:linear-gradient(135deg,#f6f6f6,#a8adb3)}
.foot-brand{left:40px;top:4150px;font:900 24px/32px 'Roboto',sans-serif;color:var(--orange)}
.social{top:4200px;width:30px;height:30px;border-radius:50%;border:2px solid #888}
.foot-col h6{font-size:20px;color:var(--white);margin-bottom:12px}
.foot-col a{display:block;color:#ccc;font-size:13px;line-height:20px;text-decoration:none}
.contact-row{display:flex;align-items:flex-start;gap:10px;font-size:13px;line-height:18px;margin-bottom:10px}
.contact-row .ico{width:26px;height:26px;border-radius:50%;background:var(--blue);display:flex;align-items:center;justify-content:center;flex:none}
.news-input{width:260px;height:34px;border-radius:18px;background:#fff;color:#777;font-size:13px;line-height:34px;padding-left:14px}
.news-btn{margin-top:8px;width:100px;height:32px;line-height:32px;font-size:13px}
.seal{left:1035px;top:4262px;width:50px;height:44px;border-radius:6px;background:var(--orange)}
.legal{left:0;top:4320px;width:1200px;height:32px;background:#000;color:#ccc;font-size:13px;text-align:center;line-height:32px}
</style>
</head>
<body>

<!-- HERO -->
<div class="abs hero-photo" role="img" aria-label="Photo of a fifth-wheel RV towed by a pickup truck on a rural road"></div>
<svg class="abs hero-curve" width="1200" height="180" viewBox="0 0 1200 180">
  <path d="M0 120 C300 60 700 40 1200 0 L1200 180 L0 180 Z" fill="#fff"/>
  <path d="M0 112 C300 50 700 32 1200 -6" stroke="#EE6A1F" stroke-width="10" fill="none"/>
</svg>

<header>
  <div class="abs brand">TKFinanceMan</div>
  <div class="abs call">
    <svg width="28" height="28" viewBox="0 0 24 24"><circle cx="12" cy="12" r="12" fill="#EE6A1F"/><path d="M8 6l2 0 1 3-1.5 1a8 8 0 0 0 4 4l1-1.5 3 1v2c0 1-1 1.5-2 1.5A10 10 0 0 1 6.5 8c0-1 .5-2 1.5-2z" fill="#fff"/></svg>
    <div><small>CALL US TODAY!</small><b>555-014-2200</b></div>
  </div>
  <a class="abs btn btn-blue quote-btn">GET A QUOTE</a>
  <nav class="abs main-nav">
    <a class="active">Home</a><a>About</a><a>FAQ</a><a>Boat Loans</a><a>RV Loans</a><a>Testimonials</a><a>News/Blog</a><a>Affiliate Program</a><a>Contact</a>
  </nav>
</header>

<div class="abs hero-arrow" style="left:20px">&#8249;</div>
<div class="abs hero-arrow" style="left:1165px">&#8250;</div>
<h1 class="abs hero-title">RV LOANS MADE EASY!</h1>
<p class="abs hero-sub">Welcome to TKFinanceMan.com, your one-stop resource for all of your RV financing needs.</p>
<a class="abs btn btn-blue hero-apply">APPLY TODAY</a>

<!-- CALCULATOR -->
<div class="abs calc-field" style="left:100px">Loan Amount <span>&#8964;</span></div>
<div class="abs calc-field" style="left:440px">Rate (APR) <span>&#8964;</span></div>
<div class="abs calc-field" style="left:780px">Term (Years) <span>&#8964;</span></div>
<a class="abs btn btn-blue calc-btn">CALCULATE PAYMENT</a>
<div class="abs coach-art" role="img" aria-label="Illustration of a motorhome"></div>

<!-- RV TYPES -->
<h2 class="abs section-title" style="top:1026px">WE FINANCE ALL TYPES OF RV'S</h2>

<article class="abs rv-card" style="left:100px;top:1116px">
  <div class="thumb" role="img" aria-label="Diesel pusher motorhome photo" style="background:linear-gradient(160deg,#f4d7a8,#8a6a45)"></div>
  <h3>Diesel Pushers</h3>
  <p>Flexible terms on luxury diesel coaches with quick approvals and rates that fit your travel budget.</p>
  <a class="btn btn-orange">APPLY NOW</a>
</article>
<article class="abs rv-card" style="left:440px;top:1116px">
  <div class="thumb" role="img" aria-label="Class A motorhome photo" style="background:linear-gradient(160deg,#d9c5a2,#3f4b36)"></div>
  <h3>Class A</h3>
  <p>Finance the full-size motorhome you want with simple paperwork and competitive fixed rates.</p>
  <a class="btn btn-orange">APPLY NOW</a>
</article>
<article class="abs rv-card" style="left:780px;top:1116px">
  <div class="thumb" role="img" aria-label="Class B camper van photo" style="background:linear-gradient(160deg,#a9cbee,#7b8a6c)"></div>
  <h3>Class B</h3>
  <p>Compact camper vans deserve easy loans too, with options for new and pre-owned units.</p>
  <a class="btn btn-orange">APPLY NOW</a>
</article>
<article class="abs rv-card" style="left:100px;top:1528px">
  <div class="thumb" role="img" aria-label="Class C motorhome in the mountains" style="background:linear-gradient(160deg,#9cc0e6,#4f6b52)"></div>
  <h3>Class C</h3>
  <p>Get on the road in a family-ready Class C with terms built around your monthly plans.</p>
  <a class="btn btn-orange">APPLY NOW</a>
</article>
<article class="abs rv-card featured" style="left:440px;top:1528px">
  <div class="thumb" role="img" aria-label="Toy hauler and boat on the water" style="background:linear-gradient(160deg,#cfe7fb,#3b7fbf)"></div>
  <h3>Toy Haulers</h3>
  <p>Bring the toys along with financing for haulers of every size, new or used, private or dealer.</p>
  <a class="btn" style="background:#fff;color:#1E88E5">APPLY NOW</a>
</article>
<article class="abs rv-card" style="left:780px;top:1528px">
  <div class="thumb" role="img" aria-label="Travel trailer photo" style="background:linear-gradient(160deg,#b6d4ef,#6e7f68)"></div>
  <h3>Travel Trailers</h3>
  <p>Low payments and long terms make towing your new travel trailer home simple and fast.</p>
  <a class="btn btn-orange">APPLY NOW</a>
</article>

<!-- ABOUT -->
<svg class="abs about-band" width="1200" height="800" viewBox="0 0 1200 800">
  <path d="M0 140 C400 20 800 0 1200 0 L1200 600 C800 640 400 700 0 800 Z" fill="#1E88E5"/>
  <path d="M0 190 C400 70 800 50 1200 50 L1200 560 C800 600 400 660 0 750 Z" fill="#3F4145"/>
</svg>
<div class="abs about-photo" role="img" aria-label="Photo of a Class C motorhome parked outdoors"></div>
<div class="abs about-copy">
  <h2 class="display">ABOUT US</h2>
  <h4>Your trusted source for RV Financing.</h4>
  <ul>
    <li><span class="tick"><svg width="12" height="12" viewBox="0 0 12 12"><path d="M2 6l3 3 5-6" stroke="#1E88E5" stroke-width="2" fill="none"/></svg></span>Loans from $25,000 - $5M</li>
    <li><span class="tick"><svg width="12" height="12" viewBox="0 0 12 12"><path d="M2 6l3 3 5-6" stroke="#1E88E5" stroke-width="2" fill="none"/></svg></span>Up to 25yrs old</li>
    <li><span class="tick"><svg width="12" height="12" viewBox="0 0 12 12"><path d="M2 6l3 3 5-6" stroke="#1E88E5" stroke-width="2" fill="none"/></svg></span>Same Day Approvals</li>
    <li><span class="tick"><svg width="12" height="12" viewBox="0 0 12 12"><path d="M2 6l3 3 5-6" stroke="#1E88E5" stroke-width="2" fill="none"/></svg></span>Quick Funding</li>
    <li><span class="tick"><svg width="12" height="12" viewBox="0 0 12 12"><path d="M2 6l3 3 5-6" stroke="#1E88E5" stroke-width="2" fill="none"/></svg></span>Private Party or Dealer</li>
    <li><span class="tick"><svg width="12" height="12" viewBox="0 0 12 12"><path d="M2 6l3 3 5-6" stroke="#1E88E5" stroke-width="2" fill="none"/></svg></span>Best Rates in the Industry</li>
  </ul>
  <p>Our goal is to make your RV purchase as quick and stress-free as possible. Our numerous lender relationships allow us to offer competitive rates and terms with quick turn-around times.</p>
  <a class="btn btn-orange">READ MORE</a>
</div>
<div class="abs van-art" role="img" aria-label="Illustration of a white Class C motorhome"></div>

<!-- MORE THAN BOATS -->
<div class="abs flag-wash" role="img" aria-label="Faint waving flag backdrop"></div>
<h2 class="abs section-title" style="top:2960px">WE FINANCE MORE THAN JUST BOATS</h2>
<p class="abs lede">At Meridian Recreational Finance, we are your one-stop resource for all marine, RV and Airplane Financing</p>

<div class="abs service" style="left:150px">
  <div class="disc"><svg width="70" height="60" viewBox="0 0 70 60"><path d="M8 36h54l-8 14H16z" fill="#fff"/><path d="M22 34V20h22l8 14z" fill="#fff"/><path d="M4 56c6-4 10-4 16 0s10 4 16 0 10-4 16 0 10 4 14 0" stroke="#fff" stroke-width="3" fill="none"/></svg></div>
  <span>Marine Financing</span>
</div>
<div class="abs service" style="left:470px">
  <div class="disc"><svg width="80" height="56" viewBox="0 0 80 56"><rect x="4" y="8" width="60" height="34" rx="4" fill="#fff"/><rect x="64" y="20" width="12" height="22" rx="3" fill="#fff"/><rect x="12" y="16" width="14" height="10" fill="#1E88E5"/><rect x="32" y="16" width="14" height="10" fill="#1E88E5"/><circle cx="20" cy="46" r="6" fill="#fff" stroke="#1E88E5" stroke-width="3"/><circle cx="56" cy="46" r="6" fill="#fff" stroke="#1E88E5" stroke-width="3"/></svg></div>
  <span>RV financing</span>
</div>
<div class="abs service" style="left:790px">
  <div class="disc"><svg width="70" height="70" viewBox="0 0 70 70"><path d="M35 4c3 0 4 4 4 8v14l26 14v6l-26-8v16l8 6v4l-12-3-12 3v-4l8-6V38L5 46v-6l26-14V12c0-4 1-8 4-8z" fill="#fff"/></svg></div>
  <span>Aircraft financing</span>
</div>
<a class="abs btn contact-btn">CONTACT US</a>

<!-- TESTIMONIALS -->
<section class="abs reviews">
  <h2 class="display">WHAT OUR CUSTOMERS SAY</h2>
  <div class="avatar" role="img" aria-label="Customer portrait"></div>
  <h5>DALE MERCER</h5>
  <div class="stars">★★★★★</div>
  <p>I just purchased a boat and used Meridian and they made the process very easy. The loan officer helped every step of the way and was always available when I had any questions. She was quick to keep me updated and streamlined the entire process of paperwork and funding. I would highly recommend using Meridian based on my purchasing experience.</p>
  <div class="abs rev-arrow" style="left:30px">&#8249;</div>
  <div class="abs rev-arrow" style="left:940px">&#8250;</div>
</section>

<!-- PARTNERS -->
<div class="abs partner-arrow" style="left:44px">&#8249;</div>
<div class="abs partner" style="left:90px"><i></i></div>
<div class="abs partner" style="left:254px"><i></i></div>
<div class="abs partner active" style="left:418px"><i></i></div>
<div class="abs partner" style="left:582px"><i></i></div>
<div class="abs partner" style="left:746px"><i></i></div>
<div class="abs partner-arrow" style="left:908px">&#8250;</div>
<div class="abs rv-art" role="img" aria-label="Illustration of a fifth-wheel trailer"></div>

<!-- FOOTER -->
<footer class="abs site-footer"></footer>
<div class="abs foot-brand">TKFinanceMan</div>
<div class="abs social" style="left:160px"></div>
<div class="abs social" style="left:200px"></div>
<div class="abs social" style="left:240px"></div>

<div class="abs foot-col" style="left:380px;top:4150px">
  <h6>Quick Links</h6>
  <div style="display:flex;gap:30px">
    <div><a>Home</a><a>About</a><a>FAQ</a><a>Boat Loans</a><a>RV Loans</a></div>
    <div><a>Testimonials</a><a>News/Blog</a><a>Affiliate Program</a><a>Contact</a></div>
  </div>
</div>
<div class="abs foot-col" style="left:600px;top:4150px;width:260px">
  <h6>Contact Us</h6>
  <div class="contact-row"><span class="ico"><svg width="12" height="14" viewBox="0 0 12 14"><path d="M6 0a5 5 0 0 1 5 5c0 4-5 9-5 9S1 9 1 5a5 5 0 0 1 5-5z" fill="#fff"/><circle cx="6" cy="5" r="2" fill="#1E88E5"/></svg></span><span>410 Harbor Loop Ste. 12, Bayview, CA 90000</span></div>
  <div class="contact-row"><span class="ico"><svg width="14" height="14" viewBox="0 0 24 24"><path d="M5 3h4l2 5-2.5 1.5a11 11 0 0 0 6 6L16 13l5 2v4c0 1-1 2-2 2A17 17 0 0 1 3 5c0-1 1-2 2-2z" fill="#fff"/></svg></span><span>(555) 014-2200</span></div>
  <div class="contact-row"><span class="ico"><svg width="14" height="12" viewBox="0 0 14 12"><rect x="1" y="1" width="12" height="10" fill="#fff"/><path d="M1 1l6 5 6-5" stroke="#1E88E5" fill="none"/></svg></span><span>info@tkfinanceman.example</span></div>
</div>
<div class="abs foot-col" style="left:900px;top:4150px">
  <h6>Newsletter</h6>
  <div class="news-input">Enter Email</div>
  <a class="btn btn-blue news-btn">SUBMIT</a>
</div>
<div class="abs seal"></div>
<div class="abs legal">Copyright © 2024 TKFinanceMan. All Rights Reserved.</div>

</body>
</html>
```